Brightwave Reach - Business Card

We need a business card for a Social Media Marketing company that specializes in online marketing for small businesses in Canada using common Social Media platforms such as Pixlora, Chatterly, Blinkpost & Quibber.

I have uploaded a copy of our logo which I would like utilized in the business card. We would like the business card to be modern yet classy design.

Our website is www.brightwavereach.ca

Industry/Entity Type

Marketing

Contact Information for Business Card

Email: info@brightwavereach.ca
Website: www.brightwavereach.ca
Telephone: 604-555-0193

Colors

Designer to choose colors to be used in the design.

Requirements
Must have
• Social Media icons on reverse
• Please add some designs with color.

```html
<!DOCTYPE html>
<html lang="en">
<head>
<meta charset="utf-8">
<title>Brightwave Reach – Business Card</title>
<link rel="stylesheet" href="https://fonts.googleapis.com/css2?family=Archivo+Black&family=Source+Sans+3:wght@400;600&display=swap">
<style>
  :root {
    --backdrop: #e9e6e1;
    --card-black: #050505;
    --card-slate: #3e4244;
    --logo-muted: #6b6b6b;
    --ink-light: #f4f4f4;
    --ink-soft: #d9dbdc;
    --accent-red: #d6352b;
    --accent-amber: #e8a33a;
    --accent-teal: #2fa79a;
    --accent-blue: #3b7dd8;
    --shadow: rgba(0, 0, 0, 0.25);
  }
  * { box-sizing: border-box; margin: 0; padding: 0; }
  html, body {
    width: 1200px;
    height: 900px;
    overflow: hidden;
    background: var(--backdrop);
  }
  .canvas {
    width: 1200px;
    height: 900px;
    display: flex;
    align-items: center;
    justify-content: center;
    gap: 40px;
  }
  .card {
    width: 540px;
    height: 309px;
    border-radius: 4px;
    box-shadow: 0 10px 24px var(--shadow);
    position: relative;
    overflow: hidden;
  }

  /* Front: black with centred wordmark and social channels */
  .card-front {
    background: var(--card-black);
    display: flex;
    flex-direction: column;
    align-items: center;
    justify-content: center;
  }
  .front-wordmark {
    font-family: "Archivo Black", "Arial Black", sans-serif;
    color: var(--logo-muted);
    font-size: 40px;
    line-height: 1.0;
    letter-spacing: 1px;
    text-align: center;
    text-transform: uppercase;
  }
  .social-list {
    position: absolute;
    left: 0;
    right: 0;
    bottom: 26px;
    display: flex;
    justify-content: center;
    gap: 22px;
    list-style: none;
    font-family: "Source Sans 3", "Myriad Pro", sans-serif;
    font-size: 13px;
    color: var(--ink-soft);
  }
  .social-item {
    display: flex;
    align-items: center;
    gap: 6px;
  }
  .social-dot {
    width: 10px;
    height: 10px;
    border-radius: 50%;
    flex: none;
  }
  .dot-pixlora { background: var(--accent-red); }
  .dot-chatterly { background: var(--accent-blue); }
  .dot-blinkpost { background: var(--accent-amber); }
  .dot-quibber { background: var(--accent-teal); }

  /* Back: slate with contact details */
  .card-back {
    background: var(--card-slate);
    padding: 44px 40px 0 46px;
  }
  .accent-band {
    position: absolute;
    left: 0;
    top: 0;
    bottom: 0;
    width: 8px;
    background: linear-gradient(to bottom, var(--accent-red), var(--accent-amber), var(--accent-teal), var(--accent-blue));
  }
  .back-wordmark {
    font-family: "Archivo Black", "Arial Black", sans-serif;
    color: var(--ink-light);
    font-size: 40px;
    line-height: 0.98;
    letter-spacing: 0.5px;
    text-transform: uppercase;
  }
  .holder {
    margin-top: 40px;
    font-family: "Source Sans 3", "Myriad Pro", sans-serif;
    color: var(--ink-light);
  }
  .holder-name {
    font-size: 17px;
    font-weight: 600;
    letter-spacing: 0.3px;
    text-transform: uppercase;
  }
  .holder-role {
    font-size: 14px;
    color: var(--ink-soft);
    margin-left: 8px;
  }
  .contact-list {
    list-style: none;
    margin-top: 16px;
    margin-left: 28px;
    font-family: "Source Sans 3", "Myriad Pro", sans-serif;
    font-size: 15px;
    color: var(--ink-light);
  }
  .contact-item {
    display: flex;
    align-items: center;
    gap: 8px;
    line-height: 22px;
  }
  .contact-icon { width: 11px; height: 11px; fill: var(--ink-light); flex: none; }
</style>
</head>
<body>
<main class="canvas">
  <section class="card card-front" aria-label="Card front">
    <div class="front-wordmark">Brightwave<br>Reach</div>
    <ul class="social-list">
      <li class="social-item"><span class="social-dot dot-pixlora"></span>Pixlora</li>
      <li class="social-item"><span class="social-dot dot-chatterly"></span>Chatterly</li>
      <li class="social-item"><span class="social-dot dot-blinkpost"></span>Blinkpost</li>
      <li class="social-item"><span class="social-dot dot-quibber"></span>Quibber</li>
    </ul>
  </section>

  <section class="card card-back" aria-label="Card back">
    <div class="accent-band"></div>
    <div class="back-wordmark">Brightwave<br>Reach</div>
    <div class="holder">
      <div class="holder-name">Marcus Ellery</div>
      <div class="holder-role">Managing Director</div>
    </div>
    <ul class="contact-list">
      <li class="contact-item">
        <svg class="contact-icon" viewBox="0 0 24 24" aria-hidden="true"><path d="M6.6 10.8a15.1 15.1 0 0 0 6.6 6.6l2.2-2.2a1 1 0 0 1 1-.25 11.4 11.4 0 0 0 3.6.57 1 1 0 0 1 1 1V20a1 1 0 0 1-1 1A17 17 0 0 1 3 4a1 1 0 0 1 1-1h3.5a1 1 0 0 1 1 1c0 1.25.2 2.45.57 3.6a1 1 0 0 1-.25 1z"/></svg>
        <span>604-555-0193</span>
      </li>
      <li class="contact-item">
        <svg class="contact-icon" viewBox="0 0 24 24" aria-hidden="true"><path d="M2 5h20L12 12.5z"/><path d="M2 7l10 7.5L22 7v12H2z"/></svg>
        <span>info@brightwavereach.ca</span>
      </li>
      <li class="contact-item">
        <svg class="contact-icon" viewBox="0 0 24 24" aria-hidden="true"><circle cx="12" cy="12" r="11"/></svg>
        <span>www.brightwavereach.ca</span>
      </li>
    </ul>
  </section>
</main>
</body>
</html>
```